Business Card Design for Software Development Company

I am looking for a business card design the incorporates my new logo (attached below).

Key information to include:
Name: Martin Quelbrook
Title: CEO
Email: martin@brightwellcivic.example
Phone: 555-218-9403
Website: www.brightwellcivic.example

NOTE: This design should be easy to edit so that we can order cards for different members of our team.

```html
<!DOCTYPE html>
<html lang="en">
<head>
<meta charset="utf-8">
<title>Brightwell Labs — Business Card</title>
<link rel="stylesheet" href="https://fonts.googleapis.com/css2?family=Montserrat:wght@600&family=Nunito:wght@400;700&display=swap">
<style>
  :root {
    --backdrop: #161616;
    --card: #232323;
    --white: #f2f2f2;
    --teal: #14ae97;
    --teal-deep: #11897a;
    --crimson: #a01e27;
    --vermilion: #d44f28;
    --orange: #e57c25;
    --peach: #f2c79a;
    --apricot: #f0b173;
  }
  * { box-sizing: border-box; margin: 0; padding: 0; }
  html, body { width: 1200px; height: 1059px; overflow: hidden; }
  body {
    background: var(--backdrop);
    position: relative;
    font-family: "Nunito", "Helvetica Neue", Arial, sans-serif;
    color: var(--white);
  }
  .card {
    position: absolute;
    left: 255px;
    width: 690px;
    height: 392px;
    background: var(--card);
    overflow: hidden;
  }
  .card--front { top: 89px; }
  .card--back { top: 547px; }

  .brand {
    position: absolute;
    left: 0; right: 0;
    display: flex;
    align-items: center;
    justify-content: center;
    gap: 14px;
    font-family: "Montserrat", "Helvetica Neue", Arial, sans-serif;
    font-weight: 600;
    color: var(--white);
    letter-spacing: -1px;
    white-space: nowrap;
  }
  .brand__mark { background: var(--orange); flex: none; }
  .card--front .brand { top: 78px; font-size: 50px; }
  .card--front .brand__mark { width: 28px; height: 28px; }
  .card--back .brand { top: 160px; font-size: 56px; }
  .card--back .brand__mark { width: 32px; height: 32px; }

  .identity {
    position: absolute;
    right: 385px;
    top: 258px;
    text-align: right;
  }
  .identity__name {
    font-weight: 700;
    font-size: 26px;
    line-height: 1;
    letter-spacing: 0.5px;
    white-space: nowrap;
  }
  .identity__first { color: var(--teal); }
  .identity__last { color: var(--orange); }
  .identity__title {
    font-size: 16px;
    margin-top: 4px;
    letter-spacing: 0.5px;
  }
  .divider {
    position: absolute;
    left: 343px;
    top: 250px;
    width: 1px;
    height: 66px;
    background: var(--teal);
  }
  .contacts {
    position: absolute;
    left: 370px;
    top: 244px;
    list-style: none;
  }
  .contacts__item {
    display: flex;
    align-items: center;
    gap: 8px;
    font-size: 17px;
    height: 28px;
    letter-spacing: 0.4px;
    white-space: nowrap;
  }
  .contacts__icon { width: 12px; height: 12px; fill: var(--orange); flex: none; }

  .stripe {
    position: absolute;
    left: 0; right: 0; bottom: 0;
    height: 16px;
    display: flex;
  }
  .stripe span { flex: 1; }
  .stripe .s1 { background: var(--teal); }
  .stripe .s2 { background: var(--teal-deep); }
  .stripe .s3 { background: var(--crimson); }
  .stripe .s4 { background: var(--vermilion); }
  .stripe .s5 { background: var(--orange); }
  .stripe .s6 { background: var(--peach); }
  .stripe .s7 { background: var(--apricot); }
</style>
</head>
<body>
  <section class="card card--front" aria-label="Card front">
    <div class="brand"><span class="brand__mark"></span>Brightwell Labs</div>

    <div class="identity">
      <p class="identity__name"><span class="identity__first">Martin</span> <span class="identity__last">Quelbrook</span></p>
      <p class="identity__title">CEO</p>
    </div>
    <div class="divider"></div>
    <ul class="contacts">
      <li class="contacts__item">
        <svg class="contacts__icon" viewBox="0 0 12 12" aria-hidden="true"><path d="M1 4.5C1 2.5 3 1.5 6 1.5s5 1 5 3v1H8.5V4.2h-5v1.3H1z"/><path d="M3 6.2h6l1.5 4.3h-9z"/></svg>
        <span>555-218-9403</span>
      </li>
      <li class="contacts__item">
        <svg class="contacts__icon" viewBox="0 0 12 12" aria-hidden="true"><path d="M1 5l5-3.5L11 5v6H1z M2.2 5.6L6 8.3l3.8-2.7" stroke="#232323" stroke-width="0.9"/></svg>
        <span>martin@brightwellcivic.example</span>
      </li>
      <li class="contacts__item">
        <svg class="contacts__icon" viewBox="0 0 12 12" aria-hidden="true"><circle cx="6" cy="6" r="5.2"/><path d="M3 3.5l2 .8.2 1.8-1.6 1.3M7.5 2.2l.4 1.6 1.8.5M7 8l1.4.4.4 1.6" stroke="#232323" stroke-width="0.9" fill="none"/></svg>
        <span>www.brightwellcivic.example</span>
      </li>
    </ul>

    <div class="stripe" aria-hidden="true">
      <span class="s1"></span><span class="s2"></span><span class="s3"></span><span class="s4"></span><span class="s5"></span><span class="s6"></span><span class="s7"></span>
    </div>
  </section>

  <section class="card card--back" aria-label="Card back">
    <div class="brand"><span class="brand__mark"></span>Brightwell Labs</div>
  </section>
</body>
</html>
```